Velmori Sciences needs high end Label Design for a revolutionary new supplement

We at Velmori Sciences are looking for a brand new Label Design for a first of its kind product called Solvenna. It is the first supplement on the market that treats grief and heartbreak. This product is unisex for both men and woman. We want the New Label to look high end and luxurious using the brand colors which are gold and burgundy. Please feel free to use other colors such as black, white, or gray to go along with it or any other colors if you feel would be a great fit! Velmori Sciences is like the Tarnwick of the supplement world, coming out with new products that will challenge the way people treat different symptoms. To Recap:

1. Product Name: SOLVENNA - the font will play a big roll
2. The Label will be placed on an all white bottle
3. Some parts of the label will be printed with foil to make parts of the label shiny and more attractive. Please keep this in mind when designing.
4. Must use our Logo. I will attach a file of our logo and of the emblem as well. Feel free to use the emblem separately if you have a great idea for it. Please let us know if you need the Logo in a different file type.
5. This all natural herbal supplement in pill form is the first to treat grief and support someone with a broken heart. The consumers purchasing this product will be going through a hard and emotional time. This is a serious product.
6. The manufacturer has included some basic instructions regarding the dye line and file types. Please do your best to meet these. If you cannot meet the guidelines please submit art work anyways. If your design is chosen we will just have the manufacturer replicate the design.

The final label should portray Solvenna and Velmori Sciences as a luxurious brand and product which was made with cutting edge science leading the way with revolutionary ideas. We want customers to feel that the product is worth every penny, because it is. As soon as they receive the product and take one look at the label, I want them to think WOW I made the right choice buying this. I have attached some Label designs that we really liked for your review.

Please feel free to message me with any questions or if you need the Logo in a different file type. Thank you all.
Updates

Please send in more entries while we take a couple days to review, we are still looking for that one design we can work with. We are getting close, thank you all!

Target Market(s)

People going through grief and heartbreak.

Font styles to use
Sans Serif
Script
Other font styles liked:
• Any font that looks good, The font for the name SOLVENNA is very important and will brand it. We hated the font used in the label we received in our first label draft (attached so you can see)

Requirements
Must have
• Must have the company Logo that says the company name
• Must have the colors Gold and Burgundy
• Must have some areas that will be the shiny foil when label is printed.
• Must say "Dietary Supplement" somewhere near the bottom along with "90 Capsules"
• I have attached a Label someone designed for us but were not really happy with. I did like the font the "Dietary supplement" and "90 Capsules" had and also where it was placed. We absolutely HATED the font used for Solvenna.
• Must look at the label design we received from the manufacturer and take into consideration the room needed to write in the directions and all the symbols such as "made in america" and "KMT Facility" Don't worry about adding these in as they will put those in before printing but keep in mind they will be added to the Final Label along with the Supplement Facts.
Nice to have
• Would like to see other colors to go with gold and burgundy suck as black, white, or gray. I have attached some Label designs that I really liked for your reference.
Should not have
• Does not need to have any other legal language, that will be applied by the the manufacturer's graphics team.

```html
<!DOCTYPE html>
<html lang="en">
<head>
<meta charset="utf-8">
<title>Solvenna Label</title>
<link rel="stylesheet" href="https://fonts.googleapis.com/css2?family=Josefin+Sans:wght@300&family=Montserrat:wght@500;700&display=swap">
<style>
  :root {
    --page: #f1f1f1;
    --label-black: #050505;
    --burgundy: #6d1524;
    --burgundy-deep: #3a0a13;
    --gold: #e2b21c;
    --gold-soft: #c99a1e;
    --ink-white: #ffffff;
  }
  html, body {
    margin: 0;
    padding: 0;
    width: 1200px;
    height: 1200px;
    overflow: hidden;
    background: var(--page);
  }
  .label {
    position: absolute;
    left: 100px;
    top: 108px;
    width: 1000px;
    height: 985px;
    background: radial-gradient(ellipse 70% 55% at 50% 52%, var(--burgundy-deep) 0%, var(--label-black) 75%);
    border-top: 9px solid var(--gold);
    border-bottom: 9px solid var(--gold);
    box-sizing: border-box;
  }
  .label-category {
    position: absolute;
    margin: 0;
    top: 74px;
    left: 0;
    right: 0;
    text-align: center;
    font-family: "Montserrat", sans-serif;
    font-weight: 500;
    font-size: 21px;
    letter-spacing: 0.02em;
    color: var(--ink-white);
  }
  .ornament {
    position: absolute;
    border-radius: 50%;
    background: radial-gradient(ellipse at center, rgba(201,154,30,0.55) 0%, rgba(109,21,36,0.45) 45%, rgba(5,5,5,0) 72%);
  }
  .ornament-top {
    left: 163px;
    top: 170px;
    width: 674px;
    height: 260px;
  }
  .ornament-bottom {
    left: 270px;
    top: 615px;
    width: 460px;
    height: 170px;
  }
  .rule-lines {
    position: absolute;
    left: 0;
    top: 0;
    width: 1000px;
    height: 985px;
  }
  .product-name {
    position: absolute;
    margin: 0;
    top: 462px;
    left: 0;
    right: 0;
    text-align: center;
    font-family: "Josefin Sans", sans-serif;
    font-weight: 300;
    font-size: 118px;
    line-height: 140px;
    letter-spacing: 0.05em;
    color: var(--ink-white);
  }
  .capsule-count {
    position: absolute;
    margin: 0;
    top: 838px;
    left: 0;
    right: 0;
    text-align: center;
    font-family: "Montserrat", sans-serif;
    font-weight: 500;
    font-size: 21px;
    color: var(--ink-white);
  }
  .capsule-count .count {
    font-weight: 700;
    font-size: 44px;
    margin-right: 6px;
    vertical-align: -6px;
  }
  .brand-mark {
    position: absolute;
    margin: 0;
    top: 918px;
    left: 0;
    right: 0;
    text-align: center;
    font-family: "Montserrat", sans-serif;
    font-weight: 500;
    font-size: 16px;
    letter-spacing: 0.2em;
    color: var(--gold);
  }
</style>
</head>
<body>
  <main class="label">
    <p class="label-category">DIETARY SUPPLEMENT</p>

    <div class="ornament ornament-top" role="img" aria-label="Gold foil scrollwork flourish above the product name"></div>
    <div class="ornament ornament-bottom" role="img" aria-label="Gold foil scrollwork flourish below the product name"></div>

    <svg class="rule-lines" viewBox="0 0 1000 985" aria-hidden="true">
      <line x1="40" y1="448" x2="960" y2="448" stroke="#e2b21c" stroke-width="3"/>
      <line x1="40" y1="454" x2="960" y2="454" stroke="#6d1524" stroke-width="2"/>
      <line x1="125" y1="604" x2="875" y2="604" stroke="#6d1524" stroke-width="2"/>
      <line x1="125" y1="610" x2="875" y2="610" stroke="#e2b21c" stroke-width="3"/>
    </svg>

    <h1 class="product-name">SOLVENNA</h1>

    <p class="capsule-count"><span class="count">90</span>CAPSULES</p>

    <p class="brand-mark">VELMORI SCIENCES</p>
  </main>
</body>
</html>
```